Social Health & Parkinson's

I need a 1-pg horizontal infographic that can be handed out to patients and providers. It needs to be scientifically sound (data provided), easy to understand, and visually pleasing. Target audience; patiens (mostly 40-90 years old) and providers (neurologists, nurses, physical therapists, naturopathic physicians, support group leaders, etc.) We need 6 of these, one for each topic listed on the website. Ideally, we'll hire the winner for 5 more similar projects and keep a theme.

Target Market(s)

Patients with Parkinson's disease, their families, care providers. To be handed out by physicians, support group leaders, etc.

Colors

Designer to choose colors to be used in the design.

Requirements
Must have
• Visually stunning. Data integrity-- keep the numbers and the figures we provide. Reference to where the data is coming from. Be thoughtful of elderly, vision issues. Teach everyone something.

```html
<!DOCTYPE html>
<html lang="en">
<head>
<meta charset="utf-8">
<title>Social Health &amp; Patient Reported Outcomes in PD</title>
<link href="https://fonts.googleapis.com/css2?family=Merriweather:wght@700;900&family=Open+Sans:ital,wght@0,400;0,600;0,700;1,400;1,600&display=swap" rel="stylesheet">
<style>
:root{
  --paper:#f6f6f6;
  --plum:#5e2a8a;
  --plum-dark:#4a1f72;
  --violet:#6a2c91;
  --green:#7dc142;
  --red:#c8213a;
  --blue:#2b3a9a;
  --sky:#c7dcef;
  --blush:#f3c5d6;
  --teal:#a9dccf;
  --ink:#222;
  --muted:#555;
}
*{box-sizing:border-box;margin:0;padding:0}
html,body{width:1200px;height:887px;overflow:hidden;background:var(--paper)}
body{font-family:"Open Sans",Arial,sans-serif;color:var(--ink)}
.sheet{width:1200px;height:887px;padding:16px;display:grid;grid-template-columns:390px 388px 390px;grid-template-rows:372px 483px;background:var(--paper)}
.panel{position:relative;overflow:hidden}
.panel-title{font-family:"Merriweather",Georgia,serif;font-weight:700;font-size:14px;line-height:1.15;color:var(--ink)}
.hero{background:var(--plum);color:#fff;padding:48px 30px}
.hero h1{font-family:"Merriweather",Georgia,serif;font-weight:900;font-size:37px;line-height:1.16}
.hero .tagline{margin-top:28px;font-style:italic;font-size:23px;line-height:1.5}
.quality{background:#fff;padding:28px 0 0 32px}
.loneliness{background:var(--blush);padding:28px 0 0 32px}
.predictors{background:var(--paper);padding:16px 10px 0 10px}
.predictors .caption{position:absolute;left:8px;right:8px;bottom:12px;font-size:9.5px;font-style:italic;text-align:center;color:var(--muted);line-height:1.3}
.social{background:var(--sky);padding:30px 18px 0 18px}
.scale-cards{display:flex;gap:6px;margin-top:8px}
.scale-card{flex:1;background:#fff;border-radius:8px;overflow:hidden;height:98px}
.scale-card h3{font-family:"Merriweather",Georgia,serif;font-size:15px;color:#fff;text-align:center;padding:4px 0}
.scale-card.satisfaction h3{background:var(--green)}
.scale-card.performance h3{background:var(--violet)}
.scale-card p{font-size:10px;font-style:italic;font-weight:600;text-align:center;padding:8px 14px;line-height:1.35}
.modifiable{background:var(--paper);padding:16px 10px 0 12px}
.modifiable .note{position:absolute;right:12px;top:76px;width:150px;font-size:9.3px;font-style:italic;text-align:right;color:var(--muted);line-height:1.3}
.modifiable .note p+p{margin-top:12px}
svg text{font-family:"Open Sans",Arial,sans-serif}
</style>
</head>
<body>
<main class="sheet">

  <section class="panel hero">
    <h1>Social Health &amp; Patient Reported Outcomes in PD</h1>
    <p class="tagline">Nurture social health.<br>Make friends.<br>Avoid loneliness.</p>
  </section>

  <section class="panel quality">
    <h2 class="panel-title">Correlation Between<br>Quality of Life and PRO- PD Score</h2>
    <svg class="bubble-chart" width="340" height="300" viewBox="0 0 340 300">
      <text transform="translate(18,130) rotate(-90)" font-size="11" font-weight="700" font-style="italic" text-anchor="middle">PRO-PD SCORE</text>
      <g font-size="9" font-style="italic" text-anchor="end">
        <text x="58" y="43">2500</text><text x="58" y="81">2000</text><text x="58" y="119">1500</text><text x="58" y="157">1000</text><text x="58" y="195">500</text>
      </g>
      <path d="M74 38 V200 H294" fill="none" stroke="var(--teal)" stroke-width="11" stroke-linecap="round"/>
      <g font-size="9" font-style="italic" text-anchor="middle">
        <text x="60" y="228">0</text><text x="86" y="228">5</text><text x="112" y="228">10</text><text x="139" y="228">15</text><text x="165" y="228">20</text><text x="192" y="228">25</text><text x="220" y="228">30</text><text x="248" y="228">35</text>
      </g>
      <text x="150" y="258" font-size="11" font-weight="700" font-style="italic" text-anchor="middle">Years Since Diagnose</text>
      <circle cx="96" cy="180" r="7" fill="#fff" stroke="var(--green)" stroke-width="3"/>
      <text x="110" y="183" font-size="5.5" font-weight="600">EXCELLENT</text>
      <circle cx="142" cy="152" r="13" fill="#e9e3ee" stroke="var(--violet)" stroke-width="4"/>
      <text x="162" y="155" font-size="5.5" font-weight="600">GOOD</text>
      <circle cx="196" cy="122" r="15" fill="#e5eaee" stroke="#1f79bf" stroke-width="4"/>
      <text x="218" y="125" font-size="5.5" font-weight="600">FAIR</text>
      <circle cx="237" cy="70" r="20" fill="#f7dfe4" stroke="var(--red)" stroke-width="5"/>
      <text x="210" y="72" font-size="5.5" font-weight="600" text-anchor="end">POOR</text>
    </svg>
  </section>

  <section class="panel loneliness">
    <h2 class="panel-title">Loneliness is Associated with<br>More Severe PD Symptoms</h2>
    <svg class="line-chart" width="350" height="300" viewBox="0 0 350 300">
      <text transform="translate(16,130) rotate(-90)" font-size="11" font-weight="700" font-style="italic" text-anchor="middle">Pro-PD Score</text>
      <g font-size="9" font-style="italic" text-anchor="end">
        <text x="38" y="57">1400</text><text x="38" y="83">1200</text><text x="38" y="109">1000</text><text x="38" y="135">800</text><text x="38" y="161">600</text><text x="38" y="187">400</text><text x="38" y="213">200</text><text x="38" y="240">0</text>
      </g>
      <path d="M46 50 V234 H300" fill="none" stroke="#222" stroke-width="1.5"/>
      <g font-size="9" font-style="italic" text-anchor="middle">
        <text x="46" y="248">0</text><text x="71" y="248">1</text><text x="96" y="248">2</text><text x="120" y="248">3</text><text x="145" y="248">4</text><text x="170" y="248">5</text><text x="195" y="248">6</text><text x="220" y="248">7</text><text x="245" y="248">8</text><text x="270" y="248">9</text><text x="295" y="248">10</text>
      </g>
      <polyline fill="none" stroke="var(--red)" stroke-width="2" points="46,107 71,122 83,108 96,115 120,100 145,88 157,74 195,88 220,100 245,60 295,62"/>
      <polyline fill="none" stroke="var(--blue)" stroke-width="2" points="46,174 71,160 83,162 96,158 120,153 132,159 157,161 170,152 195,147 220,142 245,141 295,134"/>
      <rect x="114" y="74" width="46" height="11" rx="5.5" fill="var(--red)"/>
      <text x="137" y="82.5" font-size="7.5" font-style="italic" fill="#fff" text-anchor="middle">Lonely</text>
      <rect x="228" y="140" width="46" height="11" rx="5.5" fill="var(--blue)"/>
      <text x="251" y="148.5" font-size="7.5" font-style="italic" fill="#fff" text-anchor="middle">Not Lonely</text>
      <text x="170" y="272" font-size="11" font-weight="700" font-style="italic" text-anchor="middle">Years Since Diagnose</text>
    </svg>
  </section>

  <section class="panel predictors">
    <h2 class="panel-title">Predictors of Physical Health in PD:<br>Loneliness, Not Tremor</h2>
    <svg class="predictor-chart" width="370" height="370" viewBox="0 0 370 370">
      <g font-family="Merriweather, Georgia, serif" font-size="9" font-weight="700">
        <circle cx="12" cy="22" r="8" fill="#6cae3a"/><text x="12" y="25" fill="#fff" text-anchor="middle">5</text><text x="26" y="25">Excellent</text>
        <circle cx="12" cy="51" r="8" fill="var(--green)"/><text x="12" y="54" fill="#fff" text-anchor="middle">4</text><text x="26" y="54">Very Good</text>
        <circle cx="12" cy="80" r="8" fill="#a7d37d"/><text x="12" y="83" fill="#fff" text-anchor="middle">3</text><text x="26" y="83">Good</text>
        <circle cx="12" cy="109" r="8" fill="#e0475c"/><text x="12" y="112" fill="#fff" text-anchor="middle">2</text><text x="26" y="112">Fair</text>
        <circle cx="12" cy="138" r="8" fill="var(--red)"/><text x="12" y="141" fill="#fff" text-anchor="middle">1</text><text x="26" y="141">Poor</text>
      </g>
      <rect x="128" y="4" width="220" height="150" rx="8" fill="#ececec"/>
      <g stroke="#d4d4d4" stroke-width="0.7">
        <line x1="128" y1="20" x2="348" y2="20"/><line x1="128" y1="36" x2="348" y2="36"/><line x1="128" y1="53" x2="348" y2="53"/><line x1="128" y1="69" x2="348" y2="69"/><line x1="128" y1="85" x2="348" y2="85"/><line x1="128" y1="101" x2="348" y2="101"/><line x1="128" y1="118" x2="348" y2="118"/><line x1="128" y1="134" x2="348" y2="134"/>
        <line x1="154" y1="4" x2="154" y2="154"/><line x1="177" y1="4" x2="177" y2="154"/><line x1="199" y1="4" x2="199" y2="154"/><line x1="222" y1="4" x2="222" y2="154"/><line x1="244" y1="4" x2="244" y2="154"/><line x1="267" y1="4" x2="267" y2="154"/><line x1="289" y1="4" x2="289" y2="154"/><line x1="312" y1="4" x2="312" y2="154"/><line x1="334" y1="4" x2="334" y2="154"/>
      </g>
      <g font-size="8" font-style="italic" text-anchor="end">
        <text x="120" y="21">0.8</text><text x="120" y="37">0.7</text><text x="120" y="53">0.6</text><text x="120" y="69">0.5</text><text x="120" y="86">0.4</text><text x="120" y="102">0.3</text><text x="120" y="118">0.2</text><text x="120" y="134">0.1</text><text x="110" y="154">0</text>
      </g>
      <g font-size="8" font-style="italic" text-anchor="middle">
        <text x="154" y="168">1.0</text><text x="177" y="168">1.5</text><text x="199" y="168">2.0</text><text x="222" y="168">2.5</text><text x="244" y="168">3.0</text><text x="267" y="168">3.5</text><text x="289" y="168">4.0</text><text x="312" y="168">4.5</text><text x="334" y="168">5.0</text>
      </g>
      <polyline fill="none" stroke="#9bcf6a" stroke-width="1.5" points="154,76 177,72 199,68 244,54 267,45 289,34 312,26 334,19"/>
      <polyline fill="none" stroke="#d5485e" stroke-width="1.5" points="154,37 199,83 222,100 244,122 289,126 334,134"/>
      <rect x="198" y="34" width="34" height="10" rx="5" fill="var(--green)"/>
      <text x="215" y="41.5" font-size="7" font-style="italic" fill="#fff" text-anchor="middle">Friends</text>
      <rect x="221" y="85" width="34" height="10" rx="5" fill="var(--red)"/>
      <text x="238" y="92.5" font-size="7" font-style="italic" fill="#fff" text-anchor="middle">Lonely</text>

      <rect x="36" y="188" width="242" height="102" rx="10" fill="#e9e9e9"/>
      <g font-size="8.5" font-style="italic" text-anchor="end">
        <text x="16" y="195">60</text><text x="16" y="214">50</text><text x="16" y="233">40</text><text x="16" y="253">30</text><text x="16" y="273">20</text>
      </g>
      <g font-size="8.5" font-style="italic" text-anchor="middle">
        <text x="30" y="308">0</text><text x="76" y="308">20</text><text x="122" y="308">40</text><text x="168" y="308">60</text><text x="214" y="308">80</text><text x="260" y="308">100</text>
      </g>
      <text x="140" y="326" font-size="11" font-weight="600" font-style="italic" text-anchor="middle">Withdrawn</text>
      <g fill="var(--violet)" opacity="0.9">
        <circle cx="40" cy="220" r="3"/><circle cx="44" cy="232" r="3"/><circle cx="46" cy="212" r="3"/><circle cx="48" cy="244" r="3"/><circle cx="50" cy="226" r="3"/><circle cx="52" cy="205" r="3"/><circle cx="54" cy="236" r="3"/><circle cx="56" cy="218" r="3"/><circle cx="58" cy="250" r="3"/><circle cx="60" cy="228" r="3"/>
        <circle cx="62" cy="210" r="3"/><circle cx="64" cy="240" r="3"/><circle cx="66" cy="222" r="3"/><circle cx="68" cy="203" r="3"/><circle cx="70" cy="232" r="3"/><circle cx="72" cy="215" r="3"/><circle cx="74" cy="246" r="3"/><circle cx="76" cy="226" r="3"/><circle cx="78" cy="208" r="3"/><circle cx="80" cy="236" r="3"/>
        <circle cx="82" cy="219" r="3"/><circle cx="84" cy="200" r="3"/><circle cx="86" cy="242" r="3"/><circle cx="88" cy="228" r="3"/><circle cx="90" cy="212" r="3"/><circle cx="92" cy="234" r="3"/><circle cx="94" cy="220" r="3"/><circle cx="96" cy="206" r="3"/><circle cx="98" cy="238" r="3"/><circle cx="100" cy="224" r="3"/>
        <circle cx="102" cy="214" r="3"/><circle cx="104" cy="230" r="3"/><circle cx="106" cy="244" r="3"/><circle cx="108" cy="218" r="3"/><circle cx="110" cy="208" r="3"/><circle cx="112" cy="228" r="3"/><circle cx="114" cy="236" r="3"/><circle cx="116" cy="220" r="3"/><circle cx="118" cy="212" r="3"/><circle cx="120" cy="232" r="3"/>
        <circle cx="123" cy="222" r="3"/><circle cx="126" cy="240" r="3"/><circle cx="129" cy="214" r="3"/><circle cx="132" cy="228" r="3"/><circle cx="135" cy="218" r="3"/><circle cx="138" cy="234" r="3"/><circle cx="141" cy="224" r="3"/><circle cx="144" cy="212" r="3"/><circle cx="148" cy="230" r="3"/><circle cx="152" cy="220" r="3"/>
        <circle cx="156" cy="236" r="3"/><circle cx="160" cy="226" r="3"/><circle cx="164" cy="216" r="3"/><circle cx="168" cy="230" r="3"/><circle cx="172" cy="222" r="3"/><circle cx="176" cy="234" r="3"/><circle cx="180" cy="228" r="3"/><circle cx="186" cy="224" r="3"/><circle cx="192" cy="232" r="3"/><circle cx="198" cy="226" r="3"/>
        <circle cx="206" cy="238" r="3"/><circle cx="214" cy="226" r="3"/><circle cx="222" cy="236" r="3"/><circle cx="230" cy="220" r="3"/><circle cx="50" cy="256" r="3"/><circle cx="66" cy="252" r="3"/><circle cx="94" cy="250" r="3"/><circle cx="58" cy="198" r="3"/>
      </g>
      <text x="318" y="236" font-family="Merriweather, Georgia, serif" font-size="9.5" font-weight="700" text-anchor="middle">Quality of Life</text>
      <text x="318" y="253" font-family="Merriweather, Georgia, serif" font-size="9.5" font-weight="700" text-anchor="middle">vs</text>
      <text x="318" y="270" font-family="Merriweather, Georgia, serif" font-size="9.5" font-weight="700" text-anchor="middle">Withdrawn</text>
    </svg>
    <p class="caption">Overall, individuals identifying asbeing lonely reported consistently greater PD symptom severity. Although tremor is a cardinal symptom of PD and highly visible, feeling socially withdrawn is more closely correlated to overall quality of life than tremor.</p>
  </section>

  <section class="panel social">
    <svg class="bar-chart" width="352" height="276" viewBox="0 0 352 276">
      <g stroke="#fff" stroke-width="1.2">
        <line x1="28" y1="20" x2="352" y2="20"/><line x1="28" y1="75" x2="352" y2="75"/><line x1="28" y1="130" x2="352" y2="130"/><line x1="28" y1="185" x2="352" y2="185"/><line x1="28" y1="240" x2="352" y2="240"/>
      </g>
      <g font-size="9" font-style="italic" text-anchor="start">
        <text x="0" y="23">2000</text><text x="0" y="78">1500</text><text x="0" y="133">1000</text><text x="0" y="188">500</text><text x="8" y="243">0</text>
      </g>
      <g font-family="Merriweather, Georgia, serif" font-size="11" font-weight="700" text-anchor="middle">
        <rect x="40" y="186" width="24" height="54" fill="var(--green)"/><text x="52" y="182">494</text>
        <rect x="66" y="191" width="24" height="49" fill="var(--violet)"/><text x="78" y="187">446</text>
        <rect x="106" y="167" width="24" height="73" fill="var(--green)"/><text x="118" y="163">667</text>
        <rect x="132" y="168" width="24" height="72" fill="var(--violet)"/><text x="144" y="164">653</text>
        <rect x="172" y="142" width="24" height="98" fill="var(--green)"/><text x="184" y="138">889</text>
        <rect x="198" y="139" width="24" height="101" fill="var(--violet)"/><text x="210" y="135">922</text>
        <rect x="238" y="110" width="24" height="130" fill="var(--green)"/><text x="250" y="106">1178</text>
        <rect x="264" y="104" width="24" height="136" fill="var(--violet)"/><text x="276" y="100">1233</text>
        <rect x="304" y="95" width="24" height="145" fill="var(--green)"/><text x="316" y="91">1317</text>
        <rect x="330" y="79" width="22" height="161" fill="var(--violet)"/><text x="341" y="75">1464</text>
      </g>
      <g font-size="6.5" font-style="italic" fill="#444" text-anchor="middle">
        <text x="52" y="250">n=343</text><text x="78" y="250">n=322</text><text x="118" y="250">n=607</text><text x="144" y="250">n=647</text><text x="184" y="250">n=468</text><text x="210" y="250">n=491</text><text x="250" y="250">n=269</text><text x="276" y="250">n=247</text><text x="316" y="250">n=61</text><text x="341" y="250">n=44</text>
      </g>
      <g font-size="8.5" fill="#fff" text-anchor="middle">
        <rect x="40" y="260" width="50" height="13" fill="#3a3a3a"/><text x="65" y="270">Excellent</text>
        <rect x="106" y="260" width="50" height="13" fill="#3a3a3a"/><text x="131" y="270">Very Good</text>
        <rect x="172" y="260" width="50" height="13" fill="#3a3a3a"/><text x="197" y="270">Good</text>
        <rect x="238" y="260" width="50" height="13" fill="#3a3a3a"/><text x="263" y="270">Fair</text>
        <rect x="304" y="260" width="48" height="13" fill="#3a3a3a"/><text x="328" y="270">Poor</text>
      </g>
    </svg>
    <div class="scale-cards">
      <div class="scale-card satisfaction">
        <h3>Social Satisfaction</h3>
        <p>In General, please rate how well you rate your satisfaction with your social activites and relationships</p>
      </div>
      <div class="scale-card performance">
        <h3>Social Performance</h3>
        <p>In General, please rate how well you rate your satisfaction with your social activites and roles</p>
      </div>
    </div>
  </section>

  <section class="panel modifiable">
    <h2 class="panel-title">Modifiable variables associated with risk<br>of parkinsons disease</h2>
    <svg class="diverging-chart" width="370" height="420" viewBox="0 0 370 420">
      <defs>
        <linearGradient id="benefit" x1="0" x2="1"><stop offset="0" stop-color="#fff"/><stop offset="1" stop-color="var(--violet)"/></linearGradient>
        <linearGradient id="harm" x1="0" x2="1"><stop offset="0" stop-color="#f6b7c8"/><stop offset="1" stop-color="#fff"/></linearGradient>
      </defs>
      <g font-size="9" font-style="italic" text-anchor="end">
        <text x="175" y="12">Exercize  30 + min/day, 7 days/wk</text>
        <text x="175" y="48">Exercize  30 + min/day, 6 days/wk</text>
        <text x="175" y="84">Exercize  30 + min/day, 5 days/wk</text>
        <text x="175" y="120">Exercize  30 + min/day, 4 days/wk</text>
        <text x="175" y="156">Exercize  30 + min/day, 3 days/wk</text>
        <text x="175" y="192">I cook most of my meals</text>
        <text x="175" y="228">I have a lot of friends</text>
        <text x="175" y="264">I practice stress management</text>
      </g>
      <g>
        <rect x="52" y="16" width="123" height="9" fill="url(#benefit)"/>
        <rect x="55" y="52" width="120" height="9" fill="url(#benefit)"/>
        <rect x="78" y="88" width="97" height="9" fill="url(#benefit)"/>
        <rect x="81" y="124" width="94" height="9" fill="url(#benefit)"/>
        <rect x="96" y="160" width="79" height="9" fill="url(#benefit)"/>
        <rect x="106" y="196" width="69" height="9" fill="url(#benefit)"/>
        <rect x="114" y="232" width="61" height="9" fill="url(#benefit)"/>
        <rect x="155" y="268" width="20" height="9" fill="url(#benefit)"/>
      </g>
      <g font-family="Merriweather, Georgia, serif" font-size="14" font-weight="700" fill="var(--green)" text-anchor="end">
        <text x="50" y="28">-301</text><text x="53" y="64">-292</text><text x="88" y="100">-237</text><text x="91" y="136">-229</text><text x="106" y="172">-192</text><text x="116" y="208">-168</text><text x="124" y="244">-148</text><text x="153" y="280">-48</text>
      </g>
      <g font-size="9" font-style="italic">
        <text x="176" y="300">I have a lot of stress</text>
        <text x="176" y="336">I am overweight</text>
        <text x="176" y="372">I am lonely</text>
      </g>
      <rect x="176" y="304" width="57" height="9" fill="url(#harm)"/>
      <rect x="176" y="340" width="74" height="9" fill="url(#harm)"/>
      <rect x="176" y="376" width="135" height="9" fill="url(#harm)"/>
      <g font-family="Merriweather, Georgia, serif" font-size="14" font-weight="700" fill="var(--red)" text-anchor="end">
        <text x="258" y="314">139</text><text x="276" y="350">180</text><text x="339" y="386">328</text>
      </g>
      <rect x="0" y="396" width="350" height="14" fill="#ececec"/>
      <g font-size="9" font-style="italic" text-anchor="middle">
        <text x="13" y="407">400</text><text x="54" y="407">300</text><text x="95" y="407">200</text><text x="136" y="407">100</text><text x="176" y="407">0</text><text x="217" y="407">100</text><text x="258" y="407">200</text><text x="299" y="407">300</text><text x="340" y="407">400</text>
      </g>
    </svg>
    <div class="note">
      <p>Individuals who reported feeling lonely reported greater overall PD symptom severity (+328; p=0.000), which was even higher than scores for smoking tobacco (+173; p=0.005) and having a lot of stress(+180; p=0.000).</p>
      <p>In contrast, individuals that reported having a lot of friends had reduced PD severity scores (-168; p=0.000). Notably, exercising 7 days per week was less beneficial (-301; p=0.000) than feeling lonely was detrimental.</p>
    </div>
  </section>

</main>
</body>
</html>
```